Design a Mobile App for Landscape Businesses

This project is to design the first three screens for a mobile app for Landscape and Lawncare businesses. This app will serve as a directory for homeowners to locate landscape and lawn care businesses and for landscape businesses and contractors to run their business. See the attached PDF for more information and example
Here is the link to the description https://lnkbrev.example/q7z3Kp

Target Market(s)

Landscape and lawn care business, gardeners, home owners

Industry/Entity Type

Landscape Gardening

Logo Text

Verdalink

Colors

Designer to choose colors to be used in the design.

```html
<!DOCTYPE html>
<html lang="en">
<head>
<meta charset="utf-8">
<title>Verdalink – Directory Listing</title>
<link href="https://fonts.googleapis.com/css2?family=Montserrat:wght@400;500;600&display=swap" rel="stylesheet">
<style>
  :root{
    --bg:#ffffff;
    --stage:#f4f5f7;
    --brand-blue:#3388dd;
    --button-blue:#2f7fd8;
    --text-dark:#555a60;
    --text-mid:#7b8087;
    --text-soft:#9a9ea4;
    --lawn-deep:#3f7a32;
    --lawn-light:#6fae4e;
    --tree:#8fa86f;
  }
  *{box-sizing:border-box;margin:0;padding:0}
  html,body{width:1200px;height:902px;overflow:hidden;background:var(--stage);
    font-family:"Montserrat",sans-serif;color:var(--text-dark)}
  .app-screen{position:absolute;left:390px;top:40px;width:420px;height:822px;
    background:var(--bg);border-radius:22px;overflow:hidden;
    box-shadow:0 8px 30px rgba(0,0,0,.08)}
  .app-header{height:72px;background:var(--brand-blue);display:flex;
    align-items:flex-end;justify-content:center;padding-bottom:8px}
  .brand{display:flex;align-items:center;gap:6px;background:var(--bg);
    padding:5px 12px;border-radius:14px}
  .brand-dot{width:10px;height:10px;border-radius:50%;background:var(--lawn-light)}
  .brand-name{font-size:12px;font-weight:600;color:var(--brand-blue)}
  .sort-bar{display:flex;align-items:center;gap:16px;padding:14px 18px 10px;font-size:12px;color:var(--text-mid)}
  .sort-option.is-active{background:var(--brand-blue);color:#fff;padding:5px 9px;font-weight:500}
  .listing{display:flex;gap:12px;padding:6px 18px;height:98px}
  .listing-photo{width:112px;height:86px;flex:none;
    background:linear-gradient(180deg,var(--tree) 0%,var(--tree) 38%,var(--lawn-light) 40%,var(--lawn-deep) 100%)}
  .listing-main{flex:1;display:flex;flex-direction:column;gap:3px;padding-top:6px}
  .listing-name{font-size:17px;font-weight:500;color:var(--text-dark)}
  .listing-tagline{font-size:8.5px;text-transform:uppercase;color:var(--text-soft);line-height:1.2;max-width:130px}
  .quote-button{margin-top:4px;align-self:flex-start;background:var(--button-blue);color:#fff;
    font-size:10px;padding:5px 12px;border:none;font-family:inherit;box-shadow:0 2px 4px rgba(0,0,0,.15)}
  .listing-meta{width:92px;flex:none;font-size:10px;color:var(--text-mid);padding-top:34px;line-height:1.55}
</style>
</head>
<body>
<main class="app-screen">
  <header class="app-header">
    <div class="brand"><span class="brand-dot"></span><span class="brand-name">Verdalink</span></div>
  </header>
  <nav class="sort-bar">
    <span class="sort-label">Sort by:</span>
    <span class="sort-option is-active">Distance</span>
    <span class="sort-option">Offering A Deal</span>
    <span class="sort-option">Price</span>
  </nav>
  <section class="listings">
    <article class="listing"><div class="listing-photo" role="img" aria-label="Freshly striped lawn with trees"></div><div class="listing-main"><h2 class="listing-name">Birchrow Lawn</h2><p class="listing-tagline">Every yard gets our full attention</p><button class="quote-button">Quote please</button></div><div class="listing-meta">serving<br>Maple Hollow<br>+0100555012</div></article>
    <article class="listing"><div class="listing-photo" role="img" aria-label="Freshly striped lawn with trees"></div><div class="listing-main"><h2 class="listing-name">Birchrow Lawn</h2><p class="listing-tagline">Every yard gets our full attention</p><button class="quote-button">Quote please</button></div><div class="listing-meta">serving<br>Maple Hollow<br>+0100555012</div></article>
    <article class="listing"><div class="listing-photo" role="img" aria-label="Freshly striped lawn with trees"></div><div class="listing-main"><h2 class="listing-name">Birchrow Lawn</h2><p class="listing-tagline">Every yard gets our full attention</p><button class="quote-button">Quote please</button></div><div class="listing-meta">serving<br>Maple Hollow<br>+0100555012</div></article>
    <article class="listing"><div class="listing-photo" role="img" aria-label="Freshly striped lawn with trees"></div><div class="listing-main"><h2 class="listing-name">Birchrow Lawn</h2><p class="listing-tagline">Every yard gets our full attention</p><button class="quote-button">Quote please</button></div><div class="listing-meta">serving<br>Maple Hollow<br>+0100555012</div></article>
    <article class="listing"><div class="listing-photo" role="img" aria-label="Freshly striped lawn with trees"></div><div class="listing-main"><h2 class="listing-name">Birchrow Lawn</h2><p class="listing-tagline">Every yard gets our full attention</p><button class="quote-button">Quote please</button></div><div class="listing-meta">serving<br>Maple Hollow<br>+0100555012</div></article>
    <article class="listing"><div class="listing-photo" role="img" aria-label="Freshly striped lawn with trees"></div><div class="listing-main"><h2 class="listing-name">Birchrow Lawn</h2><p class="listing-tagline">Every yard gets our full attention</p><button class="quote-button">Quote please</button></div><div class="listing-meta">serving<br>Maple Hollow<br>+0100555012</div></article>
    <article class="listing"><div class="listing-photo" role="img" aria-label="Freshly striped lawn with trees"></div><div class="listing-main"><h2 class="listing-name">Birchrow Lawn</h2><p class="listing-tagline">Every yard gets our full attention</p><button class="quote-button">Quote please</button></div><div class="listing-meta">serving<br>Maple Hollow<br>+0100555012</div></article>
  </section>
</main>
</body>
</html>
```